Podcast Cover Art for rebranded podcast - I have inspiration for the designs

I've had a podcast ("Paperboat Radio Hour") since 2018, but I'm in the process of rebranding it. I've attached the old cover art below, which I loved, but I don't need it to look like that at all. The rebranded podcast is called 'Open Window with Marnie Cole.' I've included the show description at the bottom. I've been working on various design options in Canva, but not obsessed with anything yet, but I'm attaching the ones I do like that I think just need some refining. My very favorite is the one labeled 'favorite_Open Window' so I wouldn't mind keeping that general idea but perfected by a designer. Ultimately, I want something cool, fairly clean, modern, eye catching. I'm into neutrals with maybe a pop of color, so think black, white, grey..maybe silver, and I love a pop of red..and I'm not opposed to other options for the pop color. The show is going to be inspiring, entertaining, and funny. Oh and one other idea I had but I'm not sure if it makes sense with the title and/or what the show is about..but a vinyl record with Open Window with Marnie Cole on it somehow, on a record player..not sure.

Ever wonder what it means to truly live authentically? Curious about how to embrace the unpredictability of life? Ready for some heartfelt and lighthearted conversations that inspire and entertain?
Join Marnie Cole as she dives into the raw, real, and unscripted moments of life. In each episode, Marnie brings candid conversations and genuine insights into the ups and downs we all experience. From personal growth and self-discovery to inspiring stories and valuable life lessons, "Open Window" is a space where authenticity reigns and spontaneity is celebrated.
Whether she's sharing her own journey or chatting with inspiring guests, Marnie invites you to explore the beauty of living life without a script. Expect honest reflections, thought-provoking discussions, and a refreshing perspective on navigating life's unpredictable path—all with a dash of fun and humor to keep things lively and entertaining. Step into the unscripted moments of life and tune in for a blend of depth and lightheartedness that will leave you inspired, smiling, and most importantly laughing.

Target Market(s)

25-50 year old women and men (primarily women)

Font styles to use
Sans Serif

Requirements
Should not have
• nothing too feminine or girly, nothing cheesy :)

```html
<!DOCTYPE html>
<html lang="en">
<head>
<meta charset="utf-8">
<title>Open Window with Marnie Cole — Podcast Cover</title>
<link rel="stylesheet" href="https://fonts.googleapis.com/css2?family=Bebas+Neue&family=Montserrat:wght@400;800&family=Kaushan+Script&display=swap">
<style>
  :root {
    --paper: #ffffff;
    --ink: #1b1b1b;
    --pop-red: #c40022;
  }
  html, body {
    margin: 0;
    padding: 0;
    width: 1200px;
    height: 1200px;
    overflow: hidden;
    background: var(--paper);
  }
  .cover {
    position: relative;
    width: 1200px;
    height: 1200px;
    background: var(--paper);
    overflow: hidden;
  }
  .title-rule {
    position: absolute;
    left: 97px;
    top: 0;
    width: 21px;
    height: 659px;
    background: var(--ink);
  }
  .title-top {
    position: absolute;
    left: 128px;
    top: 512px;
    margin: 0;
    font-family: "Bebas Neue", sans-serif;
    font-size: 160px;
    line-height: 1;
    color: var(--ink);
    height: 147px;
    display: flex;
    align-items: flex-end;
  }
  .photo {
    position: absolute;
    margin: 0;
  }
  .photo--laptop {
    left: 388px; top: 0; width: 304px; height: 336px;
    background: linear-gradient(160deg, #d3001c 0%, #b8001a 55%, #5a0010 100%);
  }
  .photo--garden {
    left: 388px; top: 359px; width: 304px; height: 298px;
    background: linear-gradient(135deg, #7d8a4a 0%, #a98663 45%, #4a3a2c 100%);
  }
  .photo--mirror {
    left: 713px; top: 0; width: 487px; height: 657px;
    background: linear-gradient(180deg, #b8b59c 0%, #8f8a7c 40%, #b22030 62%, #3a3534 100%);
  }
  .title-main {
    position: absolute;
    left: 96px;
    top: 664px;
    margin: 0;
    font-family: "Bebas Neue", sans-serif;
    font-size: 292px;
    line-height: 1;
    color: var(--pop-red);
    letter-spacing: 2px;
  }
  .host {
    position: absolute;
    left: 97px;
    top: 985px;
    display: flex;
    align-items: baseline;
    gap: 22px;
    margin: 0;
  }
  .host__with {
    font-family: "Kaushan Script", cursive;
    font-size: 68px;
    color: var(--pop-red);
  }
  .host__first {
    font-family: "Montserrat", sans-serif;
    font-weight: 800;
    font-size: 88px;
    letter-spacing: 10px;
    color: var(--ink);
  }
  .host__last {
    font-family: "Montserrat", sans-serif;
    font-weight: 400;
    font-size: 88px;
    letter-spacing: 14px;
    color: var(--ink);
  }
</style>
</head>
<body>
  <main class="cover">
    <div class="title-rule"></div>
    <p class="title-top">OPEN</p>

    <figure class="photo photo--laptop" role="img" aria-label="Host smiling while lying with a laptop, tinted red"></figure>
    <figure class="photo photo--garden" role="img" aria-label="Host seated outdoors in warm evening light among trees"></figure>
    <figure class="photo photo--mirror" role="img" aria-label="Host laughing in a red top leaning against a mirror in a bright room"></figure>

    <h1 class="title-main">WINDOW</h1>

    <p class="host">
      <span class="host__with">With</span>
      <span class="host__first">MARNIE</span>
      <span class="host__last">COLE</span>
    </p>
  </main>
</body>
</html>
```